Nu?c M?m G?ng (Vietnamese Ginger Fish Sauce)

Launching a bottle sauce for our restaurant. Create 2 inch (width) x 3 inch (Height) label, a unique Vietnamese design for our bottle. We want the label to show a little Vietnam in it. Maybe have a Vietnamese Ao Dai Girl (character - see attached).

Top: Nước Mắm Gừng (Vietnamese Ginger Fish Sauce)
Middle: Ao Dai girl character. Something similar to the attachment.
Bottom: Have the ingredients, Name of the restaurant and location, web address

Ingredient: Fish Sauce, Ginger, Garlic, Chili Paste, Lime, Sugar

Address: 2846 N. 7th Street, Philadelphia, PA 19023
Web Address: www.bacdaorestaurant.com

```html
<!DOCTYPE html>
<html lang="vi">
<head>
<meta charset="utf-8">
<title>Nước Mắm Gừng – Bottle Label</title>
<link rel="stylesheet" href="https://fonts.googleapis.com/css2?family=Montserrat:wght@500;600&family=Open+Sans:wght@700;800&display=swap">
<style>
  :root {
    --navy: #22265c;
    --paper: #ffffff;
    --backdrop: #ffffff;
    --figure-tint-a: #e6e7f1;
    --figure-tint-b: #cfd1e4;
  }
  * { margin: 0; padding: 0; box-sizing: border-box; }
  html, body {
    width: 1200px; height: 1200px; overflow: hidden;
    background: var(--backdrop);
  }
  .label {
    position: absolute;
    left: 233px; top: 50px;
    width: 733px; height: 1100px;
    background: var(--paper);
    overflow: hidden;
  }
  .product-tab {
    position: absolute;
    right: 0; top: 0;
    width: 268px; height: 67px;
    background: var(--navy);
    border-bottom-left-radius: 34px;
    color: var(--paper);
    font-family: "Open Sans", sans-serif;
    font-weight: 800;
    font-size: 17px;
    line-height: 21px;
    text-align: center;
    padding-top: 12px;
    letter-spacing: 0.3px;
  }
  .vertical-title {
    position: absolute;
    left: 120px; top: 448px;
    transform: translate(-50%, -50%) rotate(-90deg);
    white-space: nowrap;
    font-family: "Open Sans", sans-serif;
    font-weight: 800;
    font-size: 90px;
    line-height: 1;
    color: var(--navy);
    letter-spacing: 1px;
  }
  .ao-dai-figure {
    position: absolute;
    left: 243px; top: 74px;
    width: 362px; height: 786px;
    background: linear-gradient(180deg, var(--figure-tint-a), var(--figure-tint-b));
    border-radius: 140px 140px 30px 30px;
  }
  .restaurant-name {
    position: absolute;
    right: 45px; top: 797px;
    font-family: "Montserrat", sans-serif;
    font-weight: 600;
    font-size: 24px;
    color: var(--navy);
  }
  .footer-wave {
    position: absolute;
    left: 0; top: 860px;
    width: 733px; height: 240px;
  }
  .footer-info {
    position: absolute;
    left: 0; top: 915px;
    width: 733px;
    text-align: center;
    color: var(--paper);
    font-family: "Montserrat", sans-serif;
    font-weight: 500;
  }
  .ingredient-heading { font-size: 18px; letter-spacing: 0.5px; line-height: 24px; }
  .ingredient-list { font-size: 20px; line-height: 26px; margin-top: 7px; }
  .footer-rule {
    width: 614px; height: 2px;
    margin: 21px auto 0 59px;
    background: var(--paper);
  }
  .address { font-size: 18px; line-height: 24px; margin-top: 17px; }
  .website { font-size: 18px; font-weight: 600; line-height: 24px; margin-top: 8px; }
</style>
</head>
<body>
  <main class="label">
    <div class="product-tab">Vietnamese Ginger<br>Fish Sauce</div>

    <h1 class="vertical-title">Nước Mắm Gừng</h1>

    <div class="ao-dai-figure" role="img" aria-label="Line drawing of a woman in a flowing áo dài standing on a brush-stroke ground line"></div>

    <div class="restaurant-name">Bac Dao</div>

    <svg class="footer-wave" viewBox="0 0 733 240" aria-hidden="true">
      <path d="M0 28 C 180 40, 320 20, 420 12 C 540 4, 640 26, 733 50 L733 240 L0 240 Z" fill="var(--navy)"/>
    </svg>

    <section class="footer-info">
      <p class="ingredient-heading">INGREDIENT</p>
      <p class="ingredient-list">Fish Sauce | Ginger | Garlic | Chili Paste | Lime | Sugar</p>
      <div class="footer-rule"></div>
      <p class="address">2846 N. 7th Street, Philadelphia, PA 19023</p>
      <p class="website">www.bacdaorestaurant.com</p>
    </section>
  </main>
</body>
</html>
```